Animal Eye Clinic needs a Business card

We are a new veterinary ophthalmology practice (Ridgeline Pet Vision Care) and we need a business card designed. We only see animal eyes - we are not a regular veterinary clinic. We already have a logo. We are looking for a professional, good looking business card to hand out to our clients. We are looking for something simple but professional and contemporary. Our logo is likely the only picture/graphic that needs to be on the card.
Updates

Contact Information for Business Card

Delia Vossman, BSc, DVM, MSc, DipACVO
Veterinary Ophthalmologist

Phone: 250.418.3927
Email: ridgelinepetvisioncare@mailbox-example.net
Website: ridgelinepetvisioncare-example.net
Address: 1874 Thornbury Rd
Kelowna, BC, V1X 4M9

Colors

Designer to choose colors to be used in the design.

Requirements
Must have
• Our logo (attached)

```html
<!DOCTYPE html>
<html lang="en">
<head>
<meta charset="utf-8">
<title>Ridgeline Pet Vision Care – Business Card</title>
<link href="https://fonts.googleapis.com/css2?family=Montserrat:wght@600&family=Oswald:wght@500&family=Roboto:wght@400&display=swap" rel="stylesheet">
<style>
  :root {
    --stage: #3a3a3b;
    --card: #2b2b2c;
    --card-deep: #222223;
    --pattern-light: #4a4a4b;
    --teal: #1499aa;
    --white: #f2f2f2;
    --muted: #6a6a6b;
  }
  * { margin: 0; padding: 0; box-sizing: border-box; }
  html, body {
    width: 1200px; height: 901px; overflow: hidden;
    background: var(--stage);
  }
  .canvas {
    position: relative; width: 1200px; height: 901px;
    display: flex; flex-direction: column; align-items: center;
    justify-content: center; gap: 40px;
  }
  .card {
    position: relative; width: 620px; height: 354px;
    background: var(--card); overflow: hidden;
    box-shadow: 0 10px 30px rgba(0,0,0,.35);
  }
  /* Front */
  .front-pattern {
    position: absolute; inset: 0;
    background: linear-gradient(100deg, var(--card-deep) 0%, var(--card-deep) 45%, var(--pattern-light) 100%);
  }
  .brand {
    position: absolute; left: 200px; top: 150px;
    display: flex; align-items: center; gap: 14px;
  }
  .brand-dot {
    width: 44px; height: 44px; border-radius: 50%;
    background: var(--teal); flex: none;
  }
  .brand-name {
    font-family: "Montserrat", sans-serif; font-weight: 600;
    font-size: 21px; color: var(--teal); letter-spacing: .5px;
  }
  /* Back */
  .back-watermark {
    position: absolute; left: 230px; top: 40px; width: 300px; height: 280px;
    border-radius: 50%;
    background: radial-gradient(circle, rgba(255,255,255,.07) 0%, rgba(255,255,255,.03) 55%, rgba(255,255,255,0) 72%);
  }
  .identity {
    position: absolute; right: 338px; top: 122px; text-align: right;
  }
  .identity .name {
    font-family: "Oswald", sans-serif; font-weight: 500;
    font-size: 19px; color: var(--teal); text-transform: uppercase; letter-spacing: .3px;
  }
  .identity .role, .identity .address {
    font-family: "Roboto", sans-serif; font-size: 15px; color: var(--white);
    line-height: 1.4;
  }
  .divider {
    position: absolute; left: 298px; top: 128px; width: 1px; height: 80px;
    background: var(--muted);
  }
  .contacts {
    position: absolute; left: 312px; top: 130px; list-style: none;
    font-family: "Roboto", sans-serif; font-size: 13px; color: var(--white);
  }
  .contacts li { display: flex; align-items: center; gap: 8px; height: 26px; }
  .contacts svg { width: 12px; height: 12px; flex: none; fill: var(--teal); }
  .contacts .accent { color: var(--teal); }
  .bottom-band {
    position: absolute; left: 0; right: 0; bottom: 0; height: 10px;
    background: var(--teal);
  }
</style>
</head>
<body>
<main class="canvas">
  <section class="card card-front">
    <div class="front-pattern" role="img" aria-label="Repeating embossed logo pattern across the card"></div>
    <div class="brand">
      <span class="brand-dot"></span>
      <span class="brand-name">Ridgeline Pet Vision Care</span>
    </div>
  </section>

  <section class="card card-back">
    <div class="back-watermark" role="img" aria-label="Large faint logo mark in the background"></div>
    <div class="identity">
      <p class="name">Delia Vossman, BSc, DVM, MSc, DipACVO</p>
      <p class="role">Veterinary Ophthalmologist</p>
      <p class="address">1874 Thornbury Rd, Kelowna, BC, V1X 4M9</p>
    </div>
    <span class="divider"></span>
    <ul class="contacts">
      <li>
        <svg viewBox="0 0 24 24"><path d="M6.6 10.8a15.1 15.1 0 0 0 6.6 6.6l2.2-2.2c.3-.3.7-.4 1-.2 1.1.4 2.3.6 3.6.6.6 0 1 .4 1 1V20c0 .6-.4 1-1 1A17 17 0 0 1 3 4c0-.6.4-1 1-1h3.5c.6 0 1 .4 1 1 0 1.3.2 2.5.6 3.6.1.3 0 .7-.2 1z"/></svg>
        <span>250.418.3927</span>
      </li>
      <li>
        <svg viewBox="0 0 24 24"><path d="M2 5h20v14H2z M2 5l10 8 10-8" fill="none" stroke="#1499aa" stroke-width="2.5"/></svg>
        <span>ridgelinepetvisioncare@mailbox-example.net</span>
      </li>
      <li>
        <svg viewBox="0 0 24 24"><circle cx="12" cy="12" r="10"/></svg>
        <span>www.<span class="accent">ridgelinepetvisioncare-example</span>.net</span>
      </li>
    </ul>
    <div class="bottom-band"></div>
  </section>
</main>
</body>
</html>
```